Design a New Business Card for Our Company

We are looking for fresh, unique, and a modern business card that reflects our roots as digital marketing agency focused on SEM.

Industry/Entity Type

Marketing

Contact Information for Business Card

looking for very unique out of the box designs. clean and modern that compliments our logo

Requirements
Must have
• colors should match our logo
• Front should have name, address, email, and phone/fax of the person, phone/fax are the same number
• back should have our url

```html
<!DOCTYPE html>
<html lang="en">
<head>
<meta charset="utf-8">
<title>Brightpath Solutions — Business Card</title>
<link rel="stylesheet" href="https://fonts.googleapis.com/css2?family=PT+Sans:wght@400;700&display=swap">
<style>
  :root {
    --page-bg: #e9e9e9;
    --card-white: #ffffff;
    --brand-blue: #5f9bd5;
    --brand-grey: #a9a9a9;
    --ink-dark: #4a4a4a;
    --ink-light: #ffffff;
    --card-shadow: 0 4px 14px rgba(0, 0, 0, 0.22);
  }
  * { box-sizing: border-box; margin: 0; padding: 0; }
  html, body {
    width: 1105px;
    height: 1200px;
    overflow: hidden;
    background: var(--page-bg);
    font-family: "PT Sans", "Helvetica Neue", Arial, sans-serif;
  }
  .card {
    position: absolute;
    left: 192px;
    width: 720px;
    height: 410px;
    background: var(--card-white);
    box-shadow: var(--card-shadow);
    overflow: hidden;
  }
  .card--front { top: 146px; }
  .card--back { top: 602px; }

  .front-panel {
    position: absolute;
    inset: 0;
    width: 100%;
    height: 100%;
  }
  .front-panel__fill { fill: var(--brand-blue); }

  .person {
    position: absolute;
    left: 57px;
    top: 48px;
    color: var(--ink-light);
  }
  .person__name {
    font-size: 27px;
    font-weight: 700;
    line-height: 1.1;
  }
  .person__role {
    font-size: 19px;
    font-weight: 400;
    margin-top: 2px;
  }

  .address {
    position: absolute;
    left: 57px;
    top: 214px;
    color: var(--ink-light);
    font-size: 19px;
    line-height: 27px;
    font-style: normal;
  }

  .contact-list {
    position: absolute;
    left: 57px;
    top: 281px;
    list-style: none;
    color: var(--ink-light);
    font-size: 19px;
    line-height: 27px;
  }
  .contact-list__item {
    display: flex;
    align-items: center;
    gap: 8px;
  }
  .contact-list__icon {
    width: 19px;
    height: 19px;
    fill: var(--ink-light);
    flex: none;
  }

  .brand {
    position: absolute;
    left: 0;
    right: 0;
    top: 180px;
    display: flex;
    justify-content: center;
    align-items: center;
    gap: 14px;
  }
  .brand__dot {
    width: 30px;
    height: 30px;
    border-radius: 50%;
    background: var(--brand-blue);
  }
  .brand__name {
    font-size: 44px;
    font-weight: 700;
    color: var(--brand-blue);
    line-height: 1;
  }

  .website {
    position: absolute;
    left: 0;
    right: 0;
    top: 347px;
    text-align: center;
    color: var(--ink-dark);
    font-size: 18px;
    letter-spacing: 4px;
  }
</style>
</head>
<body>

<section class="card card--front" aria-label="Business card front">
  <svg class="front-panel" viewBox="0 0 720 410" preserveAspectRatio="none" aria-hidden="true">
    <path class="front-panel__fill"
          d="M0 0 H485 C430 40 400 110 410 190 C420 280 460 350 430 410 H0 Z"/>
  </svg>

  <div class="person">
    <h1 class="person__name">Daniel Reyes</h1>
    <p class="person__role">CEO/Founder</p>
  </div>

  <address class="address">
    412 Cedar Hollow Road<br>
    Juneau, Alaska 99801
  </address>

  <ul class="contact-list">
    <li class="contact-list__item">
      <svg class="contact-list__icon" viewBox="0 0 24 24" aria-label="Phone">
        <path d="M6.6 10.8a15.5 15.5 0 0 0 6.6 6.6l2.2-2.2c.3-.3.7-.4 1-.2 1.1.4 2.3.6 3.6.6.6 0 1 .4 1 1V20c0 .6-.4 1-1 1A17 17 0 0 1 3 4c0-.6.4-1 1-1h3.5c.6 0 1 .4 1 1 0 1.3.2 2.5.6 3.6.1.3 0 .7-.2 1z"/>
      </svg>
      <span>907 555 0148</span>
    </li>
    <li class="contact-list__item">
      <svg class="contact-list__icon" viewBox="0 0 24 24" aria-label="Fax">
        <path d="M6 3h9l3 3v4H6z M3 11h18v8H3z M7 17h10v4H7z"/>
      </svg>
      <span>907 555 0172</span>
    </li>
    <li class="contact-list__item">
      <svg class="contact-list__icon" viewBox="0 0 24 24" aria-label="Email">
        <path d="M3 6h18v12H3z" opacity="0.95"/>
        <path d="M3 6l9 7 9-7" fill="none" stroke="#5f9bd5" stroke-width="1.6"/>
      </svg>
      <span>hello@brightpathmail.com</span>
    </li>
  </ul>
</section>

<section class="card card--back" aria-label="Business card back">
  <div class="brand">
    <span class="brand__dot" aria-hidden="true"></span>
    <span class="brand__name">Brightpath Solutions</span>
  </div>
  <p class="website">www.brightpathsite.com</p>
</section>

</body>
</html>
```